Vantrel Intergrated Marketing Stationary Design Contest

We require a very professional looking stationary set to include: letterhead, compliments slip and business cards (double sided bus cards).

Files should be supplied on either Illustrator or InDesign.

We are interested in perhaps encorporating a faint watermark with the letter q or the logo, but it isnt a pre-requisite

Target Market(s)

Business owners seeking professional marketing services

Industry/Entity Type

Marketing

Requirements
Must have
• Concurrent theme wiht business cards, letterhead and comp slip. Must be an editable document for future ammendment
Should not have
• No use of times new roman or similar fonts

```html
<!DOCTYPE html>
<html lang="en">
<head>
<meta charset="utf-8">
<title>Vantrel Integrated Marketing – Stationery Set</title>
<link rel="stylesheet" href="https://fonts.googleapis.com/css2?family=PT+Sans:ital,wght@0,400;0,700;1,400;1,700&display=swap">
<style>
  :root {
    --brand-orange: #f15a29;
    --soft-orange: #f7935a;
    --ink: #231f20;
    --wordmark-grey: #4d4d4f;
    --paper: #ffffff;
    --edge: #231f20;
  }
  * { box-sizing: border-box; margin: 0; padding: 0; }
  html, body { width: 1200px; height: 1200px; overflow: hidden; background: var(--paper); }
  body { position: relative; font-family: "PT Sans", Arial, sans-serif; color: var(--ink); }

  .sheet { position: absolute; background: var(--paper); border: 1.5px solid var(--edge); }
  .letterhead { left: 224px; top: 50px; width: 602px; height: 850px; }
  .comp-slip { left: 374px; top: 338px; width: 601px; height: 283px; }
  .card-front { left: 289px; top: 974px; width: 258px; height: 158px; background: var(--brand-orange); border: none; }
  .card-back { left: 565px; top: 974px; width: 259px; height: 158px; }

  .brand { position: absolute; display: flex; align-items: center; gap: 6px; }
  .brand-dot { width: 26px; height: 26px; border-radius: 50%; background: var(--brand-orange); flex: none; }
  .brand-name { font-size: 24px; font-weight: 400; color: var(--wordmark-grey); letter-spacing: 2px; line-height: 1; }
  .letterhead .brand { left: 50%; top: 36px; transform: translateX(-50%); }
  .comp-slip .brand { left: 50%; top: 20px; transform: translateX(-50%); }
  .card-front .brand { left: 50%; top: 50%; transform: translate(-50%, -50%); gap: 9px; }
  .card-front .brand-dot { width: 42px; height: 42px; background: var(--paper); opacity: .85; }
  .card-front .brand-name { color: var(--paper); font-size: 30px; letter-spacing: 3px; }

  .slip-title { position: absolute; left: 238px; top: 55px; font-size: 12px; font-style: italic; color: var(--soft-orange); letter-spacing: .3px; }

  .footer { position: absolute; left: 0; right: 0; text-align: center; font-size: 7.4px; line-height: 1.45; }
  .letterhead .footer { bottom: 16px; }
  .comp-slip .footer { bottom: 6px; }
  .footer .company { color: var(--brand-orange); font-weight: 700; }
  .footer .office { font-style: italic; font-weight: 700; }
  .footer .row span { margin: 0 5px; }
  .footer .row .tag { color: var(--brand-orange); margin: 0 1px 0 0; }
  .footer .legal { margin-top: 2px; }
  .footer .legal span { margin: 0 8px; }

  .contact { position: absolute; left: 0; right: 0; top: 80px; text-align: center; font-size: 7px; line-height: 1.45; }
  .contact .person { color: var(--brand-orange); font-weight: 700; font-size: 10px; line-height: 1.2; }
  .contact .role { font-size: 7.2px; margin-bottom: 4px; }
  .contact .company { color: var(--brand-orange); font-weight: 700; }
  .contact .office { font-style: italic; font-size: 6.4px; }
  .contact .grid { display: grid; grid-template-columns: 1fr 1fr; width: 190px; margin: 0 auto; text-align: left; }
  .contact .tag { color: var(--brand-orange); }
</style>
</head>
<body>

<section class="sheet letterhead" aria-label="Letterhead">
  <div class="brand"><span class="brand-dot"></span><span class="brand-name">vantrel</span></div>
  <footer class="footer">
    <div class="company">Vantrel Integrated Marketing</div>
    <div class="office">Central Offices</div>
    <div>Harlow Street, Brinsford, West Yorkshire ,BN14 7QT</div>
    <div class="row">
      <span><b class="tag">W:</b> www.vantrelim.co.uk</span>
      <span><b class="tag">E:</b> enquiries@vantrelim.co.uk</span>
      <span><b class="tag">T:</b> 01632 960614</span>
      <span><b class="tag">F:</b> 01632 960611</span>
    </div>
    <div class="legal">
      <span>Company registration: 4815162</span><span>Vat No: 712 4408 51</span><span>Trading as a division of Marrowby Ltd</span>
    </div>
  </footer>
</section>

<section class="sheet comp-slip" aria-label="Compliments slip">
  <div class="brand"><span class="brand-dot"></span><span class="brand-name">vantrel</span></div>
  <div class="slip-title">WITH COMPLEMENTS</div>
  <footer class="footer">
    <div class="company">Vantrel Integrated Marketing</div>
    <div class="office">Central Offices</div>
    <div>Harlow Street, Brinsford, West Yorkshire ,BN14 7QT</div>
    <div class="row">
      <span><b class="tag">W:</b> www.vantrelim.co.uk</span>
      <span><b class="tag">E:</b> enquiries@vantrelim.co.uk</span>
      <span><b class="tag">T:</b> 01632 960614</span>
      <span><b class="tag">F:</b> 01632 960611</span>
    </div>
    <div class="legal">
      <span>Company registration: 4815162</span><span>Vat No: 712 4408 51</span><span>Trading as a division of Marrowby Ltd</span>
    </div>
  </footer>
</section>

<section class="sheet card-front" aria-label="Business card front">
  <div class="brand"><span class="brand-dot"></span><span class="brand-name">vantrel</span></div>
</section>

<section class="sheet card-back" aria-label="Business card back">
  <div class="contact">
    <div class="person">Owen Hartley</div>
    <div class="role">General Manager</div>
    <div class="company">Vantrel Integrated Marketing</div>
    <div class="office">Central Office</div>
    <div>Harlow Street, Brinsford, West Yorkshire, BN14 7QT</div>
    <div class="grid">
      <span><b class="tag">W:</b> www.vantrelim.co.uk</span>
      <span><b class="tag">E:</b> owen@vantrelim.co.uk</span>
      <span><b class="tag">T:</b> 01632 960614</span>
      <span><b class="tag">F:</b> 01632 960611</span>
    </div>
  </div>
</section>

</body>
</html>
```